Human Resource Consulting practice needs a business card design

We need a business card design (double sided colour) for our Human Resource (HR) consulting practice in regional New South Wales, australia. Our business name is Staff Compass. We support small and medium business across the Mid North Coast of New South Wales by providing them with outsourced HR support, services and products to help them achieve compliance with workplace legislation and across all areas of the employment lifecycle from recruitment to termination and everything in between. Our corporate colours are hot pink and black. The final design should communicate professionalism, trust, people focus.
I have attached the current (old) business card for your reference.

Target Market(s)

Business owners and high level managers

Industry/Entity Type

Business

Contact Information for Business Card

Name
Title
Phone no
Mobile no
Address
PO Box
email address
website

Colors
e34197

Requirements
Must have
• Tempate for changing business card personal details including Name, position title, mobile number, email address.
• Keep current logo and colours as per attached
• Logo must be presented in 2 colours or black only not white
Nice to have
• One side logo and graphic only other side logo and personal details
Should not have
• Should not be the same as the current version (attached) but a modern interpretation.
• Does not need a busy reverse side with our list of services as per current version. I feel this is too busy.
• No photos

```html
<!DOCTYPE html>
<html lang="en">
<head>
<meta charset="utf-8">
<title>Staff Compass – Business Card</title>
<link href="https://fonts.googleapis.com/css2?family=Michroma&display=swap" rel="stylesheet">
<style>
  :root {
    --hot-pink: #e312b8;
    --pink-light: #f03cc8;
    --ink: #0b0b0b;
    --ink-soft: #1b1b1b;
    --white: #ffffff;
    --grey: #b9b9b9;
    --backdrop: #e9e6e2;
  }
  * { margin: 0; padding: 0; box-sizing: border-box; }
  html, body { width: 1200px; height: 892px; overflow: hidden; }
  body {
    background: var(--backdrop);
    font-family: "Michroma", "Arial", sans-serif;
    position: relative;
  }
  .card {
    position: absolute;
    top: 156px;
    width: 340px;
    height: 580px;
    border-radius: 24px;
    overflow: hidden;
    box-shadow: 0 14px 30px rgba(0,0,0,0.18);
  }
  .card--front { left: 220px; background: var(--ink); }
  .card--back { left: 640px; background: var(--hot-pink); }

  .band { position: absolute; left: 0; width: 100%; }
  .card--front .band--top { top: 0; height: 66px; background: linear-gradient(180deg, var(--pink-light), var(--hot-pink)); }
  .card--front .band--bottom { bottom: 0; height: 96px; background: linear-gradient(180deg, var(--hot-pink), var(--pink-light)); }
  .card--back .band--bottom { bottom: 0; height: 104px; background: var(--ink); }

  .wordmark {
    position: absolute;
    display: flex;
    align-items: center;
    gap: 10px;
    font-size: 22px;
    letter-spacing: 0.5px;
    white-space: nowrap;
  }
  .wordmark__dot { width: 12px; height: 12px; background: var(--hot-pink); }
  .card--front .wordmark { top: 118px; left: 40px; color: var(--white); }
  .card--back .wordmark { top: 210px; left: 40px; color: var(--ink); font-size: 24px; }
  .card--back .wordmark__dot { background: var(--ink); }

  .person { position: absolute; top: 222px; left: 40px; }
  .person__name { color: var(--hot-pink); font-size: 20px; letter-spacing: 0.5px; }
  .person__title { color: var(--grey); font-size: 8.5px; letter-spacing: 1px; margin-top: 6px; }

  .contact { position: absolute; top: 300px; left: 40px; list-style: none; }
  .contact__item {
    display: flex; align-items: center; gap: 10px;
    color: var(--white); font-size: 10.5px; letter-spacing: 0.4px;
    height: 20px;
  }
  .contact__icon { width: 14px; height: 14px; flex: none; }
  .address { position: absolute; top: 408px; left: 40px; color: var(--white); font-size: 10px; line-height: 1.6; letter-spacing: 0.4px; }
</style>
</head>
<body>
  <section class="card card--front" aria-label="Card front">
    <div class="band band--top"></div>
    <div class="wordmark"><span class="wordmark__dot"></span>Staff Compass</div>
    <div class="person">
      <p class="person__name">Maren Holt</p>
      <p class="person__title">PRINCIPAL CONSULTANT</p>
    </div>
    <ul class="contact">
      <li class="contact__item">
        <svg class="contact__icon" viewBox="0 0 14 14"><rect width="14" height="14" rx="2" fill="var(--hot-pink)"/><path d="M4 3.5h2l.7 2-1.2.9a6 6 0 0 0 2.6 2.6l.9-1.2 2 .7v2c0 .5-.4.8-.9.8A7.5 7.5 0 0 1 3.2 4.4c0-.5.3-.9.8-.9z" fill="#fff"/></svg>
        02 6510 4821</li>
      <li class="contact__item">
        <svg class="contact__icon" viewBox="0 0 14 14"><rect width="14" height="14" rx="2" fill="var(--hot-pink)"/><rect x="4.5" y="2.5" width="5" height="9" rx="1" fill="none" stroke="#fff" stroke-width="1.2"/><circle cx="7" cy="10" r=".6" fill="#fff"/></svg>
        0411 287 536</li>
      <li class="contact__item">
        <svg class="contact__icon" viewBox="0 0 14 14"><rect width="14" height="14" rx="2" fill="var(--hot-pink)"/><rect x="3" y="6" width="8" height="5" rx="1" fill="#fff"/><rect x="4.5" y="3" width="5" height="3" fill="#fff"/></svg>
        02 6510 4822</li>
      <li class="contact__item">
        <svg class="contact__icon" viewBox="0 0 14 14"><rect width="14" height="14" rx="2" fill="var(--hot-pink)"/><circle cx="7" cy="7" r="4" fill="none" stroke="#fff" stroke-width="1.1"/><path d="M3 7h8M7 3c-2 2.5-2 5.5 0 8M7 3c2 2.5 2 5.5 0 8" fill="none" stroke="#fff" stroke-width=".9"/></svg>
        www.staffcompass.com.au</li>
      <li class="contact__item">
        <svg class="contact__icon" viewBox="0 0 14 14"><rect width="14" height="14" rx="2" fill="var(--hot-pink)"/><rect x="3" y="4" width="8" height="6" fill="none" stroke="#fff" stroke-width="1.1"/><path d="M3 4l4 3.2L11 4" fill="none" stroke="#fff" stroke-width="1.1"/></svg>
        maren@staffcompass.com.au</li>
    </ul>
    <p class="address">PO Box 218, Kestrel Bay,<br>NSW 2450</p>
    <div class="band band--bottom"></div>
  </section>

  <section class="card card--back" aria-label="Card back">
    <div class="wordmark"><span class="wordmark__dot"></span>Staff Compass</div>
    <div class="band band--bottom"></div>
  </section>
</body>
</html>
```